Business Card Design

We are a commercial real estate brokerage in San Francisco, leasing office buildings downtown.
I would like a clean, elegant look. Simple but powerful .

Industry/Entity Type

Business

Contact Information for Business Card

Derek Holloway
lic# 07258143
415.555.0172
derek@velt-commercial.example
velt-commercial.example

```html
<!DOCTYPE html>
<html lang="en">
<head>
<meta charset="utf-8">
<title>Velt Commercial — Business Card</title>
<link rel="stylesheet" href="https://fonts.googleapis.com/css2?family=Open+Sans:wght@400;600;700&display=swap">
<style>
  :root {
    --backdrop: #e6e4e1;
    --card-white: #f2f2f0;
    --card-black: #15161a;
    --slate-blue: #6f84a6;
    --text-light: #8f939b;
    --text-name: #9a9ea6;
  }
  * { margin: 0; padding: 0; box-sizing: border-box; }
  html, body {
    width: 1200px;
    height: 768px;
    overflow: hidden;
    background: var(--backdrop);
  }
  .canvas {
    position: relative;
    width: 1200px;
    height: 768px;
  }
  .card {
    position: absolute;
    top: 234px;
    width: 525px;
    height: 300px;
    border-radius: 3px;
    overflow: hidden;
    background: var(--card-white);
    box-shadow: 0 6px 18px rgba(0,0,0,0.18);
  }
  .card--front { left: 50px; }
  .card--back { left: 625px; }

  .brand-name {
    display: flex;
    align-items: center;
    font-family: "Open Sans", Arial, sans-serif;
    font-weight: 600;
    color: var(--slate-blue);
    white-space: nowrap;
  }
  .brand-name__square {
    flex: none;
    background: var(--slate-blue);
  }

  /* Front */
  .card--front .brand-name {
    position: absolute;
    inset: 0;
    justify-content: center;
    gap: 16px;
    font-size: 40px;
  }
  .card--front .brand-name__square { width: 26px; height: 26px; }

  /* Back */
  .back-shape { position: absolute; inset: 0; }
  .card--back .brand-name {
    position: absolute;
    left: 30px;
    top: 138px;
    gap: 10px;
    font-size: 21px;
  }
  .card--back .brand-name__square { width: 16px; height: 16px; }

  .contact {
    position: absolute;
    left: 292px;
    top: 88px;
    font-family: "Open Sans", Arial, sans-serif;
    color: var(--text-light);
  }
  .contact__name {
    font-weight: 700;
    font-size: 19px;
    color: var(--text-name);
    letter-spacing: 0.3px;
  }
  .contact__title {
    font-size: 11.5px;
    margin-top: 2px;
    margin-bottom: 18px;
  }
  .contact__list { list-style: none; }
  .contact__item {
    display: flex;
    align-items: center;
    gap: 9px;
    font-size: 13px;
    line-height: 22px;
    white-space: nowrap;
  }
  .contact__icon { width: 12px; height: 12px; flex: none; }
  .contact__licence { font-size: 13px; line-height: 22px; }
</style>
</head>
<body>
<main class="canvas">

  <section class="card card--front" aria-label="Business card front">
    <div class="brand-name">
      <span class="brand-name__square"></span>
      <span>Velt Commercial</span>
    </div>
  </section>

  <section class="card card--back" aria-label="Business card back">
    <svg class="back-shape" viewBox="0 0 525 300" preserveAspectRatio="none" aria-hidden="true">
      <path d="M236 0 C 290 70, 285 220, 165 300 L 525 300 L 525 0 Z" fill="var(--card-black)"/>
      <path d="M222 0 C 278 70, 274 218, 152 300" fill="none" stroke="var(--slate-blue)" stroke-width="5"/>
    </svg>

    <div class="brand-name">
      <span class="brand-name__square"></span>
      <span>Velt Commercial</span>
    </div>

    <div class="contact">
      <div class="contact__name">Derek Holloway</div>
      <div class="contact__title">Managing Director</div>
      <ul class="contact__list">
        <li class="contact__item">
          <svg class="contact__icon" viewBox="0 0 12 12" aria-hidden="true">
            <path d="M2 1 L4.5 1 L5.5 3.5 L4 4.8 C4.8 6.5 5.6 7.3 7.2 8 L8.5 6.5 L11 7.5 L11 10 C11 10.6 10.5 11 10 11 C5 10.7 1.3 7 1 2 C1 1.4 1.4 1 2 1 Z" fill="var(--text-light)"/>
          </svg>
          415.555.0172
        </li>
        <li class="contact__item">
          <svg class="contact__icon" viewBox="0 0 12 12" aria-hidden="true">
            <rect x="0.5" y="2" width="11" height="8" fill="var(--text-light)"/>
            <path d="M0.5 2 L6 6.5 L11.5 2" fill="none" stroke="var(--card-black)" stroke-width="1"/>
          </svg>
          derek@velt-commercial.example
        </li>
        <li class="contact__item">
          <svg class="contact__icon" viewBox="0 0 12 12" aria-hidden="true">
            <circle cx="6" cy="6" r="5.3" fill="var(--text-light)"/>
            <path d="M0.7 6 H11.3 M6 0.7 C3.5 3.5 3.5 8.5 6 11.3 M6 0.7 C8.5 3.5 8.5 8.5 6 11.3" fill="none" stroke="var(--card-black)" stroke-width="0.8"/>
          </svg>
          www.velt-commercial.example
        </li>
      </ul>
      <div class="contact__licence">LIC# 07258143</div>
    </div>
  </section>

</main>
</body>
</html>
```